Business Card Design Project

Business Card design based on logo.
Updates

I need business card, letterhead, envelope, and if possible, Powerpoint slide template.

On front of business card: Just logo- and  my name and title:  Harriet Lindqvist, Principal

On reverse-logo and the rest of the contact info:

4871 Quarry Lane
Davis, CA 95618
650-318-2764
hl@brackenstudyworks.example

On letterhead-Just logo at top, at bottom  the rest-very small along the bottom

On PPT slide-just the logo.

I also want to try a few other colors-I like lime/dark grey (not black) but would like to try Sienna, maybe also indigo or bright blue-green.

I forgot to add-

On the business card-switch to vertical on reverse side and put:

Reverse side-switch to vertical and list:

Harriet Lindqvist
Principal
Bracken Study Works, LLC

650-318-2764

4871 Quarry Lane
Davis, CA 95618

Harriet Lindqvist
Principal

650-318-2764

4871 Quarry Lane
Davis, CA 95618

I have another project at the same time-for Stationery. Feel free to submit to that one also.

That one includes letterhead, envelope, PPT slide, folder cover sheet-HL

Industry/Entity Type

Business

Requirements
Must have
• Must use logo-preferably lime green version-with gray, not black or just 2-tone -logo on colored background.

```html
<!DOCTYPE html>
<html lang="en">
<head>
<meta charset="utf-8">
<title>Bracken Study Works – Business Card</title>
<link rel="stylesheet" href="https://fonts.googleapis.com/css2?family=Source+Sans+3:wght@400;600;700&display=swap">
<style>
  :root {
    --backdrop: #2b2b2d;
    --card-dark: #3a3a3c;
    --card-white: #f7f7f5;
    --lime: #9ccc2f;
    --ink: #444446;
    --text-light: #e9e9e6;
    --shadow: rgba(0, 0, 0, 0.45);
  }
  * { box-sizing: border-box; margin: 0; padding: 0; }
  html, body {
    width: 1200px;
    height: 900px;
    overflow: hidden;
    background: var(--backdrop);
    font-family: "Source Sans 3", sans-serif;
  }
  .stage {
    width: 1200px;
    height: 900px;
    display: flex;
    justify-content: center;
    align-items: center;
    gap: 100px;
  }
  .card {
    position: relative;
    width: 360px;
    height: 630px;
    border-radius: 4px;
    overflow: hidden;
    background: var(--card-dark);
    box-shadow: 0 18px 40px var(--shadow);
  }

  .brand {
    display: flex;
    align-items: center;
    gap: 14px;
  }
  .brand-mark {
    width: 26px;
    height: 26px;
    background: var(--lime);
    flex: none;
  }
  .brand-name {
    font-weight: 600;
    font-size: 30px;
    line-height: 1.05;
    letter-spacing: 0.08em;
    text-transform: uppercase;
  }

  /* Front card */
  .front-brand-area {
    height: 285px;
    background: var(--card-white);
    display: flex;
    align-items: center;
    justify-content: center;
  }
  .card-front .brand-name { color: var(--ink); }
  .name-band {
    height: 100px;
    background: var(--lime);
    padding: 24px 34px 0;
  }
  .person-name {
    color: #fff;
    font-weight: 700;
    font-size: 23px;
    line-height: 1.1;
  }
  .person-title {
    color: #fff;
    font-weight: 400;
    font-size: 19px;
    margin-top: 4px;
  }

  /* Back card */
  .card-back {
    display: flex;
    flex-direction: column;
    align-items: center;
  }
  .card-back .brand { margin-top: 150px; }
  .card-back .brand-name { color: var(--text-light); }
  .contact-list {
    list-style: none;
    margin-top: 70px;
    align-self: stretch;
    padding: 0 36px;
  }
  .contact-item {
    display: flex;
    align-items: flex-start;
    gap: 14px;
    color: var(--text-light);
    font-size: 16.5px;
    line-height: 1.35;
    margin-bottom: 10px;
  }
  .contact-item.address { margin-bottom: 24px; }
  .contact-icon {
    flex: none;
    width: 22px;
    height: 22px;
    border-radius: 50%;
    background: var(--lime);
    display: flex;
    align-items: center;
    justify-content: center;
    margin-top: 1px;
  }
  .contact-icon svg { width: 12px; height: 12px; }
</style>
</head>
<body>
<main class="stage">

  <section class="card card-front" aria-label="Business card front">
    <div class="front-brand-area">
      <div class="brand">
        <span class="brand-mark"></span>
        <span class="brand-name">Bracken<br>Study Works</span>
      </div>
    </div>
    <div class="name-band">
      <p class="person-name">Harriet Lindqvist</p>
      <p class="person-title">Principal</p>
    </div>
  </section>

  <section class="card card-back" aria-label="Business card reverse">
    <div class="brand">
      <span class="brand-mark"></span>
      <span class="brand-name">Bracken<br>Study Works</span>
    </div>
    <ul class="contact-list">
      <li class="contact-item address">
        <span class="contact-icon">
          <svg viewBox="0 0 12 12"><path d="M6 1a3.4 3.4 0 0 0-3.4 3.4C2.6 7 6 11 6 11s3.4-4 3.4-6.6A3.4 3.4 0 0 0 6 1zm0 4.6a1.2 1.2 0 1 1 0-2.4 1.2 1.2 0 0 1 0 2.4z" fill="#fff"/></svg>
        </span>
        <span>4871 Quarry Lane<br>Davis, CA 95618</span>
      </li>
      <li class="contact-item">
        <span class="contact-icon">
          <svg viewBox="0 0 12 12"><path d="M3 1.2l1.6 2.2-.9 1.1c.6 1.3 1.5 2.2 2.8 2.8l1.1-.9L10.8 8 10 10.4C5.5 10.2 1.8 6.5 1.6 2z" fill="#fff"/></svg>
        </span>
        <span>650-318-2764</span>
      </li>
      <li class="contact-item">
        <span class="contact-icon">
          <svg viewBox="0 0 12 12"><rect x="2" y="4" width="8" height="6" fill="#fff"/><rect x="3.5" y="1.5" width="5" height="3" fill="none" stroke="#fff" stroke-width="1"/></svg>
        </span>
        <span>650-318-2765</span>
      </li>
      <li class="contact-item">
        <span class="contact-icon">
          <svg viewBox="0 0 12 12"><rect x="1.5" y="3" width="9" height="6.5" fill="#fff"/><path d="M1.5 3L6 6.6 10.5 3" fill="none" stroke="#9ccc2f" stroke-width="1"/></svg>
        </span>
        <span>hl@brackenstudyworks.example</span>
      </li>
      <li class="contact-item">
        <span class="contact-icon">
          <svg viewBox="0 0 12 12"><circle cx="6" cy="6" r="4.5" fill="none" stroke="#fff" stroke-width="1.2"/><path d="M1.5 6h9M6 1.5c-2 2.5-2 6.5 0 9M6 1.5c2 2.5 2 6.5 0 9" fill="none" stroke="#fff" stroke-width="0.9"/></svg>
        </span>
        <span>www.brackenstudyworks.example</span>
      </li>
    </ul>
  </section>

</main>
</body>
</html>
```